Bildevold buisnesscard

Hey :) I need a modern buisnesscard for my company Bildevold
It most have:
Dagligleder og Fotograf: Henrik Audun Strandvik

Mob: +4791264085
Epost: post@bildevold.example
Adresse: Kvernbakken9, 6040 Fjellmo

Facbook and instagram logo with text Bildevold

Bildevold logo

It Company

```html
<!DOCTYPE html>
<html lang="no">
<head>
<meta charset="utf-8">
<title>Bildevold – visittkort</title>
<link rel="stylesheet" href="https://fonts.googleapis.com/css2?family=Roboto+Condensed:wght@400;500&display=swap">
<style>
  :root{
    --backdrop:#e9e9ec;
    --charcoal:#333335;
    --silver-light:#d9dadc;
    --silver-mid:#b4b5b8;
    --stripe:#f4f4f4;
    --ink:#1e1e20;
    --rule:#444446;
    --rule-light:#77777a;
  }
  *{box-sizing:border-box;margin:0;padding:0}
  html,body{width:1200px;height:1200px;overflow:hidden;background:var(--backdrop)}
  .canvas{position:relative;width:1200px;height:1200px}
  .card{position:absolute;top:260px;width:440px;height:680px;overflow:hidden;box-shadow:0 12px 30px rgba(0,0,0,.18)}
  .card--front{left:140px}
  .card--back{left:620px}
  .card__bg{position:absolute;inset:0;width:100%;height:100%}

  .brand-name{position:absolute;left:0;right:0;text-align:center;font-family:"Roboto Condensed",sans-serif;font-weight:500;font-size:46px;line-height:1;color:var(--stripe)}
  .card--front .brand-name{top:360px}
  .card--back .brand-name{top:130px}

  .social{position:absolute;left:60px;right:60px;top:450px;font-family:"Roboto Condensed",sans-serif;font-weight:500;color:var(--stripe);font-size:19px;text-align:center}
  .social__item{display:flex;flex-direction:column;align-items:center;gap:6px;padding:14px 0}
  .social__icon{width:16px;height:16px;background:var(--stripe);border-radius:2px}
  .social__divider{border-top:2px dotted var(--rule-light);margin:4px 0}

  .contact{position:absolute;left:0;right:0;top:385px;font-family:"Roboto Condensed",sans-serif;color:var(--ink)}
  .contact__role{text-align:center;font-size:21px;line-height:26px}
  .contact__name{text-align:center;font-size:27px;line-height:32px;font-weight:500;margin-top:4px}
  .contact__rule{position:absolute;right:0;top:64px;width:60px;border-top:2px dotted var(--rule)}
  .contact__table{margin:24px 0 0 46px;font-size:19px;line-height:25px;border-collapse:collapse}
  .contact__table th{text-align:left;font-weight:500;padding-right:8px;vertical-align:top}
  .contact__table td{vertical-align:top}
  .contact__sep{padding-right:8px}

  .website{position:absolute;left:0;right:0;top:606px;text-align:center;font-family:"Roboto Condensed",sans-serif;font-size:21px;line-height:26px;color:var(--ink)}
  .website__rule{position:absolute;width:70px;border-top:2px dotted var(--rule)}
  .website__rule--top{left:0;top:592px}
  .website__rule--bottom{right:0;top:644px}
</style>
</head>
<body>
<main class="canvas">

  <section class="card card--front" aria-label="Forside">
    <svg class="card__bg" viewBox="0 0 440 680" preserveAspectRatio="none" aria-hidden="true">
      <defs>
        <linearGradient id="silverTop" x1="0" y1="0" x2="0" y2="1">
          <stop offset="0" stop-color="#b4b5b8"/>
          <stop offset="1" stop-color="#d9dadc"/>
        </linearGradient>
      </defs>
      <rect width="440" height="680" fill="url(#silverTop)"/>
      <polygon points="0,250 250,195 440,300 440,680 0,680" fill="#333335"/>
      <polygon points="0,264 250,209 440,314 440,680 0,680" fill="#f4f4f4"/>
      <polygon points="0,276 250,221 440,326 440,680 0,680" fill="#333335"/>
    </svg>
    <div class="brand-name">Bildevold</div>
    <div class="social">
      <div class="social__item"><span class="social__icon"></span>Bildevold</div>
      <div class="social__divider"></div>
      <div class="social__item"><span class="social__icon"></span>Bildevold</div>
    </div>
  </section>

  <section class="card card--back" aria-label="Bakside">
    <svg class="card__bg" viewBox="0 0 440 680" preserveAspectRatio="none" aria-hidden="true">
      <defs>
        <linearGradient id="silverBottom" x1="0" y1="0" x2="0" y2="1">
          <stop offset="0" stop-color="#d9dadc"/>
          <stop offset=".6" stop-color="#e4e4e6"/>
          <stop offset="1" stop-color="#b4b5b8"/>
        </linearGradient>
      </defs>
      <rect width="440" height="680" fill="url(#silverBottom)"/>
      <polygon points="0,0 440,0 440,330 270,372 0,282" fill="#333335"/>
      <polygon points="0,0 440,0 440,318 270,360 0,270" fill="#f4f4f4"/>
      <polygon points="0,0 440,0 440,304 270,346 0,256" fill="#333335"/>
    </svg>
    <div class="brand-name">Bildevold</div>
    <div class="contact">
      <p class="contact__role">Dagligleder og Fotograf:</p>
      <p class="contact__name">Henrik Audun Strandvik</p>
      <span class="contact__rule"></span>
      <table class="contact__table">
        <tr><th>Mob</th><td class="contact__sep">:</td><td>+4791264085</td></tr>
        <tr><th>Epost</th><td class="contact__sep">:</td><td>post@bildevold.example</td></tr>
        <tr><th>Adresse:</th><td></td><td>Kvernbakken9, 6040<br>Fjellmo</td></tr>
      </table>
    </div>
    <span class="website__rule website__rule--top"></span>
    <p class="website">www.bildevold.example</p>
    <span class="website__rule website__rule--bottom"></span>
  </section>

</main>
</body>
</html>
```